Volbrey Inc Business Card

Looking to get an updated business card for a Contract Machining company (www.volbreyinc.example) - looking for a clean design the portrays the technical nature of the business - colors can follow the website design and be in any combination that makes sense (red black, white, metallic or silver) - logos attached for use also. Would like space for: Name, title, business phone (555 214-3086), cell phone , website (www.volbreyinc.example) - possibly QR code could be integrated for website (designer choice), business address - 418 Harlow Bend, Corvell Springs, ZX 48199 (cards will be for 4 employees, I will either need to modify a template or I can provide individual information)
Target Market(s)
Aerospace, defense and medical device manufacturing companies that need machining
Industry/Entity Type
Machining for aerospace, defense, medical
Contact Information for Business Card
Name, Title, Business Phone, Cell Phone, email, business website and business address
Look and feel

```html
<!DOCTYPE html>
<html lang="en">
<head>
<meta charset="utf-8">
<title>Volbrey Inc Business Card</title>
<link rel="stylesheet" href="https://fonts.googleapis.com/css2?family=Montserrat:wght@400;600;700&display=swap">
<style>
  :root {
    --brand-red: #b01e23;
    --ink: #1a1a1a;
    --paper: #ffffff;
    --backdrop: #e4e2e3;
  }
  * { box-sizing: border-box; margin: 0; padding: 0; }
  html, body {
    width: 1200px; height: 1108px; overflow: hidden;
    background: var(--backdrop);
    font-family: "Montserrat", Arial, sans-serif;
    color: var(--ink);
  }
  .card {
    position: absolute; left: 229px;
    width: 755px; height: 461px;
    background: var(--paper);
  }
  .card--front { top: 56px; }
  .card--back { top: 575px; height: 443px; }

  .brand-mark {
    position: absolute; left: 183px; top: 143px;
    width: 155px; text-align: center;
  }
  .brand-mark__circle {
    width: 155px; height: 155px; border-radius: 50%;
    background: var(--brand-red);
  }
  .brand-mark__name {
    margin-top: 10px;
    font-weight: 700; font-size: 21px; letter-spacing: 0.3px;
    color: var(--brand-red); white-space: nowrap;
  }

  .divider {
    position: absolute; left: 372px; top: 143px;
    width: 2px; height: 220px; background: var(--brand-red);
  }

  .contact { position: absolute; left: 394px; top: 140px; }
  .contact__name {
    font-weight: 700; font-size: 28px; line-height: 1.1;
    color: var(--brand-red);
  }
  .contact__title { font-size: 17px; margin-top: 1px; }
  .contact__address { font-size: 17px; line-height: 1.25; margin-top: 16px; }
  .contact__list { list-style: none; margin-top: 14px; }
  .contact__item {
    display: flex; align-items: center; gap: 8px;
    font-size: 17px; line-height: 25px;
  }
  .contact__icon { width: 16px; height: 16px; flex: none; fill: var(--brand-red); }

  .back-mark {
    position: absolute; left: 231px; top: 75px;
    width: 293px; height: 293px; border-radius: 50%;
    background: var(--brand-red);
    display: flex; align-items: center; justify-content: center;
  }
  .back-mark__name {
    font-weight: 700; font-size: 30px; letter-spacing: 0.5px;
    color: var(--paper); white-space: nowrap;
  }
</style>
</head>
<body>
  <section class="card card--front">
    <div class="brand-mark">
      <div class="brand-mark__circle"></div>
      <div class="brand-mark__name">VOLBREY INC</div>
    </div>

    <div class="divider"></div>

    <div class="contact">
      <div class="contact__name">Dana Whitfield</div>
      <div class="contact__title">Owner</div>
      <div class="contact__address">418 Harlow Bend,<br>Corvell Springs, ZX 48199</div>
      <ul class="contact__list">
        <li class="contact__item">
          <svg class="contact__icon" viewBox="0 0 24 24" aria-hidden="true"><path d="M6.6 10.8a15.1 15.1 0 0 0 6.6 6.6l2.2-2.2a1 1 0 0 1 1-.25 11.4 11.4 0 0 0 3.6.57 1 1 0 0 1 1 1V20a1 1 0 0 1-1 1A17 17 0 0 1 3 4a1 1 0 0 1 1-1h3.5a1 1 0 0 1 1 1c0 1.25.2 2.45.57 3.57a1 1 0 0 1-.25 1z"/></svg>
          555 214-3086
        </li>
        <li class="contact__item">
          <svg class="contact__icon" viewBox="0 0 24 24" aria-hidden="true"><path d="M2 8c0-2 4-4 10-4s10 2 10 4v2h-5V8H7v2H2z"/><path d="M5 12h14l2 8H3z"/></svg>
          555 214-3086
        </li>
        <li class="contact__item">
          <svg class="contact__icon" viewBox="0 0 24 24" aria-hidden="true"><path d="M2 5h20v14H2z M2 5l10 8 10-8" fill="none" stroke="#b01e23" stroke-width="2"/><path d="M2 5h20l-10 8z"/></svg>
          info@volbreyinc.example
        </li>
        <li class="contact__item">
          <svg class="contact__icon" viewBox="0 0 24 24" aria-hidden="true"><circle cx="12" cy="12" r="10" fill="none" stroke="#b01e23" stroke-width="2"/><path d="M2 12h20M12 2c3 3 3 17 0 20M12 2c-3 3-3 17 0 20" fill="none" stroke="#b01e23" stroke-width="1.6"/></svg>
          www.volbreyinc.example
        </li>
      </ul>
    </div>
  </section>

  <section class="card card--back">
    <div class="back-mark">
      <div class="back-mark__name">VOLBREY INC</div>
    </div>
  </section>
</body>
</html>
```